zorvan lumet website design

An IT support and IT Security Company - just use dummy text for now for the design. Examples of sites we like the looks and feel of but need it more professional feel are like: www.kelbrovault.uk.com , www.pravok.co.uk, www.quenthardy.com/professional/, www.vur.com, www.melvish.com,

Best to message me if you have any questions

Target Market(s)

small to medium UK based companies that require IT support services

Industry/Entity Type

It Company

Contact Information for Business Card

use dummy name, telephone and email for now, will provide details later.

Logo Text

zorvan lumet (and then below the logo it should say "your IT, networks and security partner")

Coding

Coded - Design and coding required

Number of Pages Required

5+ page

Colors

Designer to choose colors to be used in the design.

Requirements
Must have
• must be professional, yet simple and clear that this is a serious IT support and IT security company.
Nice to have
• 1)The website homepage must have professional quality pictures of IT support or London city skyline or any picture that projects friendly business partners, professionalism and ready to serve.
• 2) Home page needs to include tabs for following pages 'Services' , 'About Us' , 'Contact Us' 'Home'
• 3) Website built customised using wordpress is ideal and easy for us to manage.
• more room for boxed options from homepage (with pic or image in background)
Should not have
• no checkout trolleys or payment options.

```html
<!DOCTYPE html>
<html lang="en">
<head>
<meta charset="utf-8">
<title>zorvan lumet</title>
<link rel="stylesheet" href="https://fonts.googleapis.com/css2?family=Mulish:wght@400;600;700&family=Noto+Sans:wght@400;700&display=swap">
<style>
:root{
  --accent:#29a9cf;
  --ink:#2b2b2b;
  --body:#6a6a6a;
  --grey-band:#ebebeb;
  --white:#ffffff;
  --rule:#d6d6d6;
  --footer-bar:#333333;
}
*{margin:0;padding:0;box-sizing:border-box}
html,body{width:1200px;height:2500px;overflow:hidden;background:var(--white)}
body{position:relative;font-family:"Mulish",sans-serif;color:var(--body)}
.block{position:absolute;left:0;width:1200px}
.abs{position:absolute}
h1,h2,h3{font-family:"Noto Sans",sans-serif;color:var(--ink);font-weight:700}
.accent{color:var(--accent)}

/* header */
.site-header{top:0;height:105px;background:var(--white)}
.brand{left:80px;top:26px;font-family:"Mulish",sans-serif;font-weight:700;font-size:40px;color:var(--accent);letter-spacing:.5px}
.main-nav{right:78px;top:42px;display:flex;gap:38px;font-size:17px;color:#555;text-transform:uppercase}
.main-nav .current{color:var(--accent)}

/* hero */
.hero{top:105px;height:562px;background:linear-gradient(135deg,#e3e9ee 0%,#cfd8df 40%,#dfe5ea 70%,#c9d2d9 100%)}
.hero-title{left:0;width:1200px;top:194px;text-align:center;font-size:48px;letter-spacing:.5px}
.hero-actions{left:0;width:1200px;top:290px;display:flex;justify-content:center;gap:12px}
.btn{display:inline-flex;align-items:center;justify-content:center;height:47px;border-radius:24px;font-size:20px;text-transform:uppercase;font-family:"Mulish",sans-serif}
.btn-solid{width:175px;background:var(--accent);color:var(--white)}
.btn-outline{width:177px;border:2px solid var(--accent);color:var(--accent);background:rgba(255,255,255,.35)}

/* services tabs */
.services-tabs{top:667px;height:155px;background:var(--white);border:1px solid var(--rule);box-shadow:0 2px 4px rgba(0,0,0,.12)}
.services-tabs h2{position:absolute;left:0;width:1200px;top:24px;text-align:center;font-size:42px}
.tab{top:100px;width:400px;text-align:center;font-size:25px}
.tab-security{left:138px;color:var(--accent)}
.tab-support{left:662px;color:#444}
.tab-divider{left:599px;top:98px;width:2px;height:42px;background:#999}

/* feature */
.feature{top:822px;height:416px;background:var(--grey-band)}
.feature-visual{left:75px;top:75px;width:522px;height:278px;border-radius:10px 10px 4px 4px;background:linear-gradient(135deg,#bfe6f5 0%,#4fb8e6 50%,#1f7fc0 100%)}
.feature h3{left:668px;top:118px;font-size:33px}
.feature p{left:668px;top:172px;width:410px;font-size:15.5px;line-height:25px}

/* welcome */
.welcome{top:1238px;height:354px;background:var(--white)}
.welcome h2{left:0;width:1200px;top:55px;text-align:center;font-size:37px}
.welcome-rule{left:565px;top:119px;width:72px;height:3px;background:var(--accent)}
.welcome-copy{left:200px;top:145px;width:800px;text-align:center;font-size:16px;line-height:25px}
.welcome-copy p+p{margin-top:17px}

/* blog */
.blog{top:1592px;height:416px;background:var(--grey-band)}
.blog h2{left:0;width:1200px;top:38px;text-align:center;font-size:42px}
.post{top:113px;width:468px;height:230px;background:var(--grey-band);border:1px solid #cfcfcf}
.post-one{left:95px}
.post-two{left:632px}
.post-image{left:0;top:0;width:208px;height:228px}
.post-one .post-image{background:linear-gradient(135deg,#c9a58a 0%,#8a5a4a 45%,#5d7f9c 100%)}
.post-two .post-image{background:linear-gradient(135deg,#d8dde2 0%,#8e9aa5 50%,#4b5560 100%)}
.post-date{width:62px;height:70px;background:var(--accent);color:var(--white);text-align:center;padding-top:6px}
.post-one .post-date{left:146px;top:30px}
.post-two .post-date{left:146px;top:123px}
.post-date .day{display:block;font-size:27px;line-height:32px}
.post-date .month{display:block;font-size:14px}
.post-body{left:232px;top:33px;width:205px}
.post-title{font-size:18px;line-height:27px;color:#222;font-family:"Mulish",sans-serif;font-weight:400}
.post-excerpt{margin-top:8px;font-size:14.5px;line-height:25px}

/* call to action */
.cta{top:2008px;height:147px;background:var(--accent)}
.cta-btn{left:315px;top:54px;width:177px;height:45px;border-radius:23px;background:var(--white);color:var(--accent);font-size:20px;display:flex;align-items:center;justify-content:center;text-transform:uppercase}
.cta-text{left:516px;top:50px;font-family:"Noto Sans",sans-serif;font-weight:700;font-size:34px;letter-spacing:1px;color:var(--white)}

/* footer */
.site-footer{top:2155px;height:292px;background:linear-gradient(135deg,#eef1f3 0%,#e4e8eb 50%,#eceff1 100%)}
.footer-col{top:50px}
.footer-col h3{font-size:27px;color:#3a3a3a}
.col-links{left:80px}
.col-contact{left:440px}
.col-news{left:802px}
.link-list{list-style:none;margin-top:14px}
.link-list li{display:flex;align-items:center;font-size:15.5px;color:#555;height:35.5px}
.link-list li::before{content:"";width:13px;height:13px;border-radius:50%;background:var(--accent);margin-right:12px}
.contact-list{list-style:none;margin-top:18px}
.contact-list li{display:flex;font-size:15.5px;line-height:25px;color:#555;margin-bottom:12px}
.contact-list svg{flex:none;margin:3px 14px 0 0}
.news-note{margin-top:18px;font-size:15.5px;color:#555}
.news-field{margin-top:14px;width:268px;height:46px;background:var(--white);border:1px solid #ccc;font-size:15px;color:#555;padding:12px 10px}
.news-btn{margin-top:12px;width:165px;height:45px;background:var(--accent);color:var(--white);font-family:"Noto Sans",sans-serif;font-weight:700;font-size:20px;display:flex;align-items:center;justify-content:center;letter-spacing:.5px}

.footer-bar{top:2447px;height:53px;background:var(--footer-bar);color:#e5e5e5;font-size:15.5px;display:flex;align-items:center;justify-content:center}
</style>
</head>
<body>

<header class="block site-header">
  <div class="abs brand">zorvan lumet</div>
  <nav class="abs main-nav">
    <span class="current">Home</span><span>About</span><span>Services</span><span>Contact</span>
  </nav>
</header>

<section class="block hero" role="img" aria-label="Photo of a bright IT support office with smiling staff wearing headsets at their computers">
  <h1 class="abs hero-title">Lorem Ipsum is simply dummy.</h1>
  <div class="abs hero-actions">
    <span class="btn btn-solid">Know More</span>
    <span class="btn btn-outline">Contact Us</span>
  </div>
</section>

<section class="block services-tabs">
  <h2>Our <span class="accent">Services</span></h2>
  <div class="abs tab tab-security">IT security</div>
  <div class="abs tab-divider"></div>
  <div class="abs tab tab-support">IT support</div>
</section>

<section class="block feature">
  <div class="abs feature-visual" role="img" aria-label="Illustration of a laptop showing a glowing padlock surrounded by network security icons"></div>
  <h3 class="abs">IT security</h3>
  <p class="abs">Lorem Ipsum is simply dummy text of the printing and typesetting industry. Lorem Ipsum has been the industry's standard dummy text ever since the 1500s, when an unknown printer took a galley of type and scrambled it to make a type specimen book.</p>
</section>

<section class="block welcome">
  <h2 class="abs">Welcome to zorvan lumet</h2>
  <div class="abs welcome-rule"></div>
  <div class="abs welcome-copy">
    <p>Lorem Ipsum is simply dummy text of the printing and typesetting industry. Lorem Ipsum has been the industry's standard dummy text ever since the 1500s, when an unknown printer took a galley of type and scrambled it to make a type specimen book.</p>
    <p>It has survived not only five centuries, but also the leap into electronic typesetting, remaining essentially unchanged. It was popularised in the 1960s with the release of Dravelon sheets containing Lorem Ipsum.</p>
  </div>
</section>

<section class="block blog">
  <h2 class="abs">Latest <span class="accent">Blog</span></h2>
  <article class="abs post post-one">
    <div class="abs post-image" role="img" aria-label="Photo of a woman working at a computer showing a cyber security screen"></div>
    <div class="abs post-date"><span class="day">29</span><span class="month">APR</span></div>
    <div class="abs post-body">
      <div class="post-title">Lorem Ipsum is simply dummy text.</div>
      <div class="post-excerpt">Lorem Ipsum is simply dummy text of the printing and typesetting industry. Lorem Ipsum has been.</div>
    </div>
  </article>
  <article class="abs post post-two">
    <div class="abs post-image" role="img" aria-label="Photo of a support engineer with a headset typing at a laptop in an office"></div>
    <div class="abs post-date"><span class="day">29</span><span class="month">APR</span></div>
    <div class="abs post-body">
      <div class="post-title">Lorem Ipsum is simply dummy text.</div>
      <div class="post-excerpt">Lorem Ipsum is simply dummy text of the printing and typesetting industry. Lorem Ipsum has been.</div>
    </div>
  </article>
</section>

<section class="block cta">
  <div class="abs cta-btn">Click Here</div>
  <div class="abs cta-text">or call 020 7946 0321.</div>
</section>

<footer class="block site-footer" role="img" aria-label="Faded photo of an office team at their desks behind the footer content">
  <div class="abs footer-col col-links">
    <h3>Useful Links</h3>
    <ul class="link-list">
      <li>Home</li><li>About Us</li><li>Services</li><li>Contact</li>
    </ul>
  </div>
  <div class="abs footer-col col-contact">
    <h3>Contact Info</h3>
    <ul class="contact-list">
      <li style="width:250px">
        <svg width="16" height="22" viewBox="0 0 16 22"><path d="M8 0C3.6 0 0 3.5 0 7.9 0 13.5 8 22 8 22s8-8.5 8-14.1C16 3.5 12.4 0 8 0z" fill="#29a9cf"/><circle cx="8" cy="8" r="3" fill="#fff"/></svg>
        <span>Lorem Ipsum is simply dummy text of the printing and.</span>
      </li>
      <li>
        <svg width="17" height="17" viewBox="0 0 24 24"><path d="M6.6 10.8c1.4 2.8 3.8 5.1 6.6 6.6l2.2-2.2c.3-.3.7-.4 1-.2 1.1.4 2.3.6 3.6.6.6 0 1 .4 1 1V20c0 .6-.4 1-1 1C10.6 21 3 13.4 3 4c0-.6.4-1 1-1h3.5c.6 0 1 .4 1 1 0 1.3.2 2.5.6 3.6.1.3 0 .7-.2 1z" fill="#29a9cf"/></svg>
        <span>020 7946 0321</span>
      </li>
      <li>
        <svg width="18" height="14" viewBox="0 0 18 14"><rect x="1" y="1" width="16" height="12" rx="1.5" fill="none" stroke="#29a9cf" stroke-width="2"/><path d="M1.5 2l7.5 6 7.5-6" fill="none" stroke="#29a9cf" stroke-width="2"/></svg>
        <span>info@zorvanlumet.com</span>
      </li>
    </ul>
  </div>
  <div class="abs footer-col col-news">
    <h3>Newsletter</h3>
    <div class="news-note">Subscribe to Our Newsletter</div>
    <div class="news-field">Enter Your Email</div>
    <div class="news-btn">SUBSCRIBE</div>
  </div>
</footer>

<div class="block footer-bar">2018 ©zorvanlumet- All Rights Reserved.</div>

</body>
</html>
```